Personal training and nutrition business needs business card design

We need a business card that outlays our services and invites potential customers to join our team and take the first step to a healthier and more enjoyable life. We cater for any level of fitness and specialize in weight loss and conditioning, strength training, muscle gain and strength endurance. Whether you are just starting off or need some help getting to the next level of your journey we are here to get the job done.
We specialize in one on one or one on two personal training sessions and each program will be custom made to suit individual fitness goals of our clients

```html
<!DOCTYPE html>
<html lang="en">
<head>
<meta charset="utf-8">
<title>Stride &amp; Pulse — Business Card</title>
<link rel="stylesheet" href="https://fonts.googleapis.com/css2?family=Oswald:wght@500;600&family=Roboto:wght@400&family=Saira:ital,wght@1,700&display=swap">
<style>
  :root {
    --backdrop: #2c2c2e;
    --card: #1b1b1d;
    --emboss: #3b3b3e;
    --ink-light: #ececec;
    --ink-soft: #d6d6d6;
    --purple: #7b45b0;
    --orchid: #a2509f;
    --band-deep: #5a3a8e;
    --band-pink: #9c4f9b;
  }
  * { margin: 0; padding: 0; box-sizing: border-box; }
  html, body {
    width: 1200px; height: 1138px; overflow: hidden;
    background: var(--backdrop);
  }
  .canvas { position: relative; width: 1200px; height: 1138px; }

  .card {
    position: absolute;
    background: var(--card);
    border-radius: 13px;
    overflow: hidden;
    box-shadow: 0 6px 16px rgba(0,0,0,0.35);
  }

  /* Front side */
  .card-front { left: 274px; top: 186px; width: 622px; height: 374px; }
  .front-brand {
    position: absolute; left: 0; right: 0; top: 78px;
    display: flex; flex-direction: column; align-items: center; gap: 22px;
  }
  .front-brand .brand-dot {
    width: 96px; height: 96px; border-radius: 50%;
    background: var(--emboss);
  }
  .front-brand .brand-name {
    font-family: "Oswald", sans-serif; font-weight: 600;
    font-size: 40px; letter-spacing: 3px; line-height: 1;
    color: var(--emboss);
  }
  .front-tagline {
    position: absolute; left: 0; right: 0; top: 335px;
    text-align: center;
    font-family: "Oswald", sans-serif; font-weight: 500;
    font-size: 13px; letter-spacing: 1.2px;
    color: var(--orchid);
  }

  /* Back side */
  .card-back { left: 276px; top: 608px; width: 618px; height: 374px; }
  .back-brand {
    position: absolute; left: 56px; top: 92px; width: 224px;
    display: flex; flex-direction: column; align-items: center; gap: 20px;
  }
  .back-brand .brand-dot {
    width: 86px; height: 86px; border-radius: 50%;
    background: linear-gradient(135deg, var(--purple), var(--orchid));
  }
  .back-brand .brand-name {
    font-family: "Oswald", sans-serif; font-weight: 600;
    font-size: 34px; letter-spacing: 2px; line-height: 1.05;
    color: var(--ink-light); text-align: center;
  }

  .contact { position: absolute; left: 340px; top: 72px; font-family: "Roboto", sans-serif; color: var(--ink-light); }
  .contact .person-name {
    font-family: "Saira", sans-serif; font-style: italic; font-weight: 700;
    font-size: 25px; letter-spacing: 1px; line-height: 1;
    color: var(--purple); margin-left: 2px;
  }
  .contact .person-role { font-size: 16px; margin-top: 8px; }
  .contact-list { list-style: none; margin-top: 25px; }
  .contact-list li {
    display: flex; align-items: center; gap: 12px;
    font-size: 16px; height: 24.5px;
  }
  .contact-list svg { width: 16px; height: 16px; fill: var(--purple); flex: none; margin-left: 2px; }
  .address { font-size: 16px; line-height: 24px; margin-top: 6px; }

  .footer-band { position: absolute; left: 0; bottom: 0; width: 618px; height: 46px; }
  .footer-text {
    position: absolute; right: 19px; bottom: 14px;
    font-family: "Roboto", sans-serif; font-size: 16px; color: var(--ink-soft);
  }
</style>
</head>
<body>
<div class="canvas">

  <section class="card card-front" aria-label="Card front">
    <div class="front-brand">
      <span class="brand-dot"></span>
      <span class="brand-name">STRIDE &amp; PULSE</span>
    </div>
    <p class="front-tagline">PERSONAL TRAINING.&nbsp; NUTRITION. MOTIVATION</p>
  </section>

  <section class="card card-back" aria-label="Card back">
    <div class="back-brand">
      <span class="brand-dot"></span>
      <span class="brand-name">STRIDE<br>&amp; PULSE</span>
    </div>

    <div class="contact">
      <h1 class="person-name">MARCUS REYES</h1>
      <p class="person-role">Personal Trainer</p>
      <ul class="contact-list">
        <li>
          <svg viewBox="0 0 16 16" aria-hidden="true"><path d="M2 5c0-2 3-3 6-3s6 1 6 3v1h-3V4.8C10 4.3 9 4 8 4s-2 .3-3 .8V6H2z M4 7h8l2 6H2z M8 8.5a2 2 0 1 0 0 4 2 2 0 0 0 0-4z"/></svg>
          <span>+1 (555) 014-2387</span>
        </li>
        <li>
          <svg viewBox="0 0 16 16" aria-hidden="true"><path d="M1 3h14v10H1z M2.5 4.5 8 9l5.5-4.5v-.2H2.5z" fill-rule="evenodd"/></svg>
          <span>marcus@stridepulse.com</span>
        </li>
        <li>
          <svg viewBox="0 0 16 16" aria-hidden="true"><path d="M8 1a7 7 0 1 0 0 14A7 7 0 0 0 8 1zm0 1.5c.8 0 1.7 1.7 2 4H6c.3-2.3 1.2-4 2-4zM2.6 6.5h2c-.1.5-.1 1-.1 1.5s0 1 .1 1.5h-2a5.6 5.6 0 0 1 0-3zm3.4 3h4c-.3 2.3-1.2 4-2 4s-1.7-1.7-2-4zm5.4 0c.1-.5.1-1 .1-1.5s0-1-.1-1.5h2a5.6 5.6 0 0 1 0 3z"/></svg>
          <span>www.stridepulse.com</span>
        </li>
      </ul>
      <p class="address">1428 Cedar Ridge Lane<br>Austin Texas 78704</p>
    </div>

    <svg class="footer-band" viewBox="0 0 618 46" aria-hidden="true">
      <defs>
        <linearGradient id="band-strip" x1="0" x2="1">
          <stop offset="0" stop-color="var(--band-pink)"/>
          <stop offset="1" stop-color="#8a4795"/>
        </linearGradient>
      </defs>
      <rect x="0" y="30" width="330" height="16" fill="url(#band-strip)"/>
      <polygon points="315,46 343,0 618,0 618,46" fill="var(--band-deep)"/>
    </svg>
    <p class="footer-text">Personal Training | Nutrition | Motivation</p>
  </section>

</div>
</body>
</html>
```